Cruise Booking Website

Cruise search and booking website

This project is a redesign of a cruise booking website we did a few years ago.

The current website is located here: http://voyage.pylonworks.example/en/

It's not fully functional but gives you ad idea how miserable the old design was.

All the information about cruises, cruise lines, destinations, ports and shore excursions will be similar to http://www.sailquest.example/
Actual search pages (form, results, single result, sailing and cabin selection, ship info, booking) will have EXACTLY the same info as sailquest.example

We like the style of http://harborfleetdesk.example, it's quite modern, good spacing, not overloaded with information. So you can use it as an example of what we like, not what we want as a final result for us. Please, don't copy it. The result should not be possible to resemble the harborfleetdesk.example, because our site has to be unique. This is important!
If you submit a design that clearly reminds another cruise site it will be rejected!

Also the mockup provided is just to give you the basic structure and show what information has to be present on the page. It doesn't mean the layout has to be the same as a mockup. The layout is up to the designer.

I've updated the mockup to be more generic so it doesn't confuse you:
https://files.boxvault.example/s/k7m2qp9wz4hx/Home%20page.png

When you're adding social sharing icons like plazanet/chirpline you have to use chinese ones instead:
https://files.boxvault.example/s/t3nr8vx5lc2e/chinese-social-icons.png
Originals: http://minilk.example/qR7t

We'll start with home page first and after it's approved inner pages can be designed.

I know the cost of the project doesn't look high, but the task is straight forward and doesn't require to be very original, it's better to follow existing design and layout patterns that proved to work well.
That's why I encourage you to choose a template to build the design on top of one of https://themeparlor.example/ themes if it will save the design work, will be easier and faster for you. So it will be more like a customization than a new design from scratch.

Mockups, site map and logo files:
- https://files.boxvault.example/sh/h48dm2rs73fkpw/QvnbW2Xz8e

Website tree:
- https://sheets.papernest.example/document/d/7xPqR2mLw9sTk4VbN8cHj3YzA6eUf5GdKo1iMnBv/edit?usp=sharing
Updates

So far a lot of designs are just copying http://www.harborfleetdesk.example/ - we don't like it!

We like the style of harborfleetdesk.example, it's quite modern, good spacing, not overloaded with information. So you can use it as an example of what we like, not what we want as a final result for us. Please, don't copy it. The result should not be possible to resemble the harborfleetdesk.example, because our site has to be unique. This is important!

Target Market(s)

Chinese travellers

Industry/Entity Type

Build

Requirements
Must have
• * White, blue and red
* Large spacing, not too much information cramped into a small space like sailquest.example or the current website
* More "hidden" info in popups, tabs and so on, so not to many things are visible at the same time
* Compatible with kestrel scaffold styling (for easier coding):
- http://kestrelkit.codeshelf.example/scaffold/index.html
- http://skinmarket.example/
* Feel free to propose to build the design on top of one of https://themeparlor.example/ themes if it will save the design work, will be easier and faster for you

```html
<!DOCTYPE html>
<html lang="en">
<head>
<meta charset="utf-8">
<title>Bluewake – Miami-Florida, USA</title>
<link href="https://fonts.googleapis.com/css2?family=PT+Sans:wght@400;700&display=swap" rel="stylesheet">
<style>
:root{
  --blue-dark:#0b4f8c;
  --blue:#1a6cb0;
  --panel:#2a7cbf;
  --orange:#f7941d;
  --orange-light:#fbb040;
  --text:#6a6a6a;
  --row:#e9e9e9;
  --footer:#3f79ae;
  --footer-bottom:#386da0;
  --white:#fff;
}
*{box-sizing:border-box;margin:0;padding:0}
html,body{width:1191px;height:1200px;overflow:hidden}
body{font-family:"PT Sans",sans-serif;background:radial-gradient(ellipse at 50% 40%,#eaf2fa 0%,#bcd4ea 45%,#4f86ba 80%,#2c6aa5 100%);position:relative;color:var(--text)}
.page{position:absolute;left:179px;top:0;width:834px;height:1200px;background:var(--white)}
.abs{position:absolute}
/* header */
.brand{left:12px;top:34px;display:flex;align-items:center;gap:8px}
.brand-dot{width:44px;height:44px;border-radius:50%;background:var(--blue)}
.brand-name{font-size:34px;font-weight:700;color:var(--blue);line-height:1}
.brand-url{font-size:9px;font-weight:700;color:var(--blue);letter-spacing:.5px}
.auth{left:610px;top:17px;font-size:11px;color:var(--blue)}
.auth span{margin:0 8px}
.social{left:717px;top:13px;display:flex;gap:4px}
.social i{display:block;width:22px;height:22px;border-radius:4px}
.call{left:450px;top:48px;display:flex;gap:8px;align-items:center}
.call-ico{width:30px;height:30px}
.call-num{font-size:19px;font-weight:700;color:var(--blue);line-height:1}
.call-txt{font-size:15px;color:#333;line-height:1.2}
.search{left:621px;top:65px;width:197px;height:22px;border:1px solid #ccc;border-radius:2px;font-size:8px;color:#888;padding:5px 10px}
.search svg{position:absolute;right:6px;top:4px}
.nav{left:0;top:111px;width:834px;height:34px;background:linear-gradient(#1e86d0,#0a5ea6);display:flex}
.nav a{display:flex;align-items:center;justify-content:center;color:var(--white);font-size:10.5px;font-weight:700;text-decoration:none;border-right:1px solid rgba(0,0,0,.15)}
.nav a.active{background:linear-gradient(#3ab0ee,#1c8ad6)}
/* sidebar */
.finder{left:18px;top:164px;width:245px;height:346px;background:var(--panel);border:2px solid #4a93d0;color:#e8f2fb}
.finder h2{font-size:22px;font-weight:400;color:var(--white);padding:16px 0 6px 22px;border-bottom:1px solid #5b9ed6;margin:0 2px}
.label{position:absolute;font-size:12px;line-height:14px}
.field{position:absolute;height:23px;background:linear-gradient(#f2f2f2,#d9d9d9);border-radius:2px;font-size:9px;color:#333;padding:6px 9px}
.field::after{content:"";position:absolute;right:0;top:0;width:20px;height:23px;border-left:1px solid #bbb;background:linear-gradient(#eee,#d0d0d0)}
.field b{position:absolute;right:6px;top:5px;width:0;height:0;border:3px solid transparent;border-bottom-color:#777;z-index:1}
.field b+b{top:12px;border-bottom-color:transparent;border-top-color:#777}
.check{position:absolute;left:20px;top:272px;font-size:9px;display:flex;align-items:center;gap:4px}
.check i{width:11px;height:11px;background:#e4e4e4;border-radius:1px}
.btn-search{position:absolute;left:19px;top:294px;width:208px;height:33px;background:linear-gradient(var(--orange-light),var(--orange));border:1px solid #d87a10;border-radius:2px;color:var(--white);font-size:15px;font-weight:700;display:flex;align-items:center;justify-content:center}
.news{left:18px;top:532px;width:245px;height:294px;background:linear-gradient(#2f86c8,#1c6aad);color:var(--white)}
.news-photo{position:absolute;left:11px;top:13px;width:223px;height:132px;background:var(--white);padding:5px}
.news-photo div{width:100%;height:100%;background:linear-gradient(#3fa3d8,#d9c9a8 70%,#f0e5d2)}
.news h3{position:absolute;left:20px;top:156px;font-size:13px}
.news p{position:absolute;left:20px;top:178px;font-size:8.5px}
.email{position:absolute;left:20px;top:203px;width:213px;height:22px;background:var(--white);border:1px solid #ccc;border-radius:2px;font-size:9px;color:#888;padding:5px 47px}
.btn-sub{position:absolute;left:21px;top:237px;width:86px;height:22px;background:var(--blue-dark);border-radius:2px;font-size:10px;display:flex;align-items:center;justify-content:center}
.rules{position:absolute;left:23px;top:271px;font-size:10.5px}
/* main */
.crumbs{left:292px;top:164px;font-size:10px;color:var(--blue);display:flex;gap:7px}
.title{left:287px;top:190px;width:527px;height:32px;background:linear-gradient(#1a75c0,#0b4f8c);border-radius:2px;color:var(--white);font-size:12.5px;font-weight:700;padding:8px 16px}
.photo{left:287px;top:238px;width:242px;height:225px;border:1px solid #ddd;padding:3px;background:var(--white)}
.photo div{width:100%;height:100%;background:linear-gradient(135deg,#b9b2a6,#d9cfc0 50%,#8d8a80)}
.facts{left:550px;top:239px;width:260px;font-size:7.5px;text-transform:uppercase;color:#666}
.facts div{display:flex;justify-content:space-between;background:var(--row);height:21.5px;align-items:center;padding:0 9px;margin-bottom:1px}
.facts div.tall{height:31px;align-items:flex-start;padding-top:7px}
.tabs{left:287px;top:491px;display:flex;gap:1px}
.tabs span{height:31px;width:115px;background:linear-gradient(var(--orange-light),var(--orange));color:var(--white);font-size:8.5px;display:flex;align-items:center;justify-content:center;border-radius:2px 2px 0 0}
.tabs span.on{width:123px;background:linear-gradient(#1a75c0,#0b4f8c)}
.tab-body{left:287px;top:522px;width:527px;height:305px;border:1px solid #ddd}
.tab-photo{position:absolute;left:17px;top:21px;width:191px;height:130px;border:1px solid #ddd;padding:3px;background:var(--white)}
.tab-photo div{width:100%;height:100%;background:linear-gradient(#9cc4e6,#d5dee2 45%,#5b8c5a 60%,#2d8fb8 80%)}
.tab-text{position:absolute;font-size:8.6px;line-height:15.3px;color:var(--text)}
/* partners */
.partners-h{left:15px;top:853px;font-size:15px;font-weight:700;color:var(--blue)}
.arrows{left:780px;top:854px;display:flex;gap:3px}
.arrows i{width:16px;height:16px;background:#ddd;display:flex;align-items:center;justify-content:center}
.partners{left:16px;top:884px;display:flex;gap:13px}
.partners span{width:123px;height:62px;border:1px solid #ddd;border-radius:2px;display:flex;align-items:center;justify-content:center}
.partners span i{display:block;width:70px;height:18px;border-radius:3px}
/* footer */
.footer{left:0;top:967px;width:834px;height:189px;background:var(--footer);color:var(--white)}
.fcol{position:absolute;top:26px}
.fcol h4{font-size:13.5px;margin-bottom:12px}
.fcol li{list-style:none;font-size:8.6px;line-height:18.7px}
.about-logo{position:absolute;left:0;top:30px;width:84px;height:82px;background:var(--white);border:1px solid #ccc;display:flex;flex-direction:column;align-items:center;justify-content:center;gap:4px}
.about-logo i{width:34px;height:34px;border-radius:50%;background:var(--blue)}
.about-logo b{font-size:10px;color:var(--blue)}
.about-text{position:absolute;left:101px;top:34px;width:110px;font-size:10.5px;line-height:15.3px}
.contact p{font-size:11px;line-height:16px}
.contact .line{display:flex;align-items:center;gap:6px;font-size:10.5px;margin-top:6px}
.bottom{left:0;top:1156px;width:834px;height:44px;background:var(--footer-bottom);color:var(--white);font-size:8.5px;display:flex;align-items:center;justify-content:center}
</style>
</head>
<body>
<div class="page">
  <header>
    <div class="abs brand"><span class="brand-dot"></span><div><div class="brand-name">Bluewake</div><div class="brand-url">www.bluewake.example</div></div></div>
    <div class="abs auth">Sign in<span>|</span>Signup</div>
    <div class="abs social" aria-label="Social links">
      <i style="background:#e0322b"></i><i style="background:#2ea8dd"></i><i style="background:#f28c14"></i><i style="background:#d8342f"></i>
    </div>
    <div class="abs call">
      <svg class="call-ico" viewBox="0 0 30 30"><circle cx="15" cy="15" r="13.5" fill="#f4f4f4" stroke="#999"/><path d="M11 8c-2 1-3 3-2 6 1 4 4 7 7 8 2 1 4 0 5-1l-3-3-2 1c-2-1-3-3-4-4l1-2z" fill="#666"/></svg>
      <div><div class="call-num">400 555 018</div><div class="call-txt">Call Us Today!</div></div>
    </div>
    <div class="abs search">SEARCH :<svg width="12" height="12" viewBox="0 0 12 12"><circle cx="5" cy="5" r="4" fill="none" stroke="#bbb" stroke-width="1.3"/><path d="M8 8l3 3" stroke="#bbb" stroke-width="1.5"/></svg></div>
    <nav class="abs nav">
      <a class="active" style="width:85px">HOME</a><a style="width:120px">DESTINATIONS</a><a style="width:107px">CRUISE LINES</a><a style="width:109px">CRUISE INFO</a><a style="width:80px">DEALS</a><a style="width:132px">ONLINE BOOKING</a><a style="width:106px">CONTACT US</a><a style="width:95px;border:0">BLOG</a>
    </nav>
  </header>

  <aside class="abs finder">
    <h2>Find Your Cruise</h2>
    <span class="label" style="left:20px;top:58px">Destination</span>
    <div class="field" style="left:20px;top:74px;width:203px">Destination name<b></b><b></b></div>
    <span class="label" style="left:21px;top:104px">Length</span>
    <span class="label" style="left:131px;top:104px">Month</span>
    <div class="field" style="left:20px;top:119px;width:91px">Length Area</div>
    <div class="field" style="left:131px;top:119px;width:91px"><b></b><b></b></div>
    <span class="label" style="left:18px;top:151px">Cruise Lines</span>
    <div class="field" style="left:18px;top:167px;width:206px">Any Cruise line<b></b><b></b></div>
    <span class="label" style="left:19px;top:203px;font-size:13.5px">Number of Travelers</span>
    <span class="label" style="left:21px;top:226px">Age 25+</span>
    <span class="label" style="left:131px;top:226px">Age 0 to 24</span>
    <div class="field" style="left:20px;top:242px;width:88px">5<b></b><b></b></div>
    <div class="field" style="left:131px;top:242px;width:88px">0<b></b><b></b></div>
    <div class="check"><i></i>Check for senior rates</div>
    <div class="btn-search">Search Cruises</div>
  </aside>

  <aside class="abs news">
    <div class="news-photo"><div role="img" aria-label="Photo of a smiling senior couple relaxing on pool loungers"></div></div>
    <h3>Cruise Deals Newsletter</h3>
    <p>Subscribe to the best Cruise deals Now!</p>
    <div class="email">Email :</div>
    <div class="btn-sub">Subscribe</div>
    <div class="rules">Contest Rules</div>
  </aside>

  <main>
    <div class="abs crumbs"><span>HOME</span><svg width="6" height="10" viewBox="0 0 6 10"><path d="M1 1l4 4-4 4" fill="none" stroke="#999" stroke-width="1.3"/></svg><span>BREADCRUMBS</span></div>
    <h1 class="abs title">MIAMI-FLORIDA, USA</h1>
    <div class="abs photo"><div role="img" aria-label="Photo of a young couple laughing in a sunny old town street"></div></div>
    <div class="abs facts">
      <div><span>Country</span><span>USA</span></div>
      <div><span>State/Region</span><span>Florida</span></div>
      <div><span>Government</span><span>United States</span></div>
      <div><span>Time Zone</span><span>-5 GMT</span></div>
      <div><span>Language</span><span>English / Spanish</span></div>
      <div><span>Capital</span><span>Washington,D.C</span></div>
      <div><span>Langtitude</span><span>-80,11'38</span></div>
      <div><span>Latitude</span><span>-80,11'38</span></div>
      <div><span>Est. Population</span><span>381264</span></div>
      <div class="tall"><span>Currency<br>Second</span><span>US Doller</span></div>
    </div>
    <div class="abs tabs"><span class="on">TAB ONE</span><span>TAB TWO</span><span>TAB THREE</span><span>TAB FOUR</span></div>
    <div class="abs tab-body">
      <div class="tab-photo"><div role="img" aria-label="Aerial photo of a city beach with high-rise hotels and turquoise sea"></div></div>
      <p class="tab-text" style="left:228px;top:14px;width:285px">Seabright Cruise Line has sailed for many years and is a well-loved name at sea. A Seabright cruise is all about creating a relaxed, memorable holiday, and every ship is designed to keep the good times going. On a Seabright ship there is always so much to do. On deck there are pools, waterslides, mini golf, a seaside theatre and activities galore to keep kids and adults of all ages entertained. Kids love the youth club, and for a little quiet time adults can relax on the adults-only sun deck or be pampered in the onboard spa. Dining options are varied and include casual dining on deck, traditional dining, sushi and elegant dining in the</p>
      <p class="tab-text" style="left:17px;top:170px;width:495px">Seabright Cruise Line has sailed for many years and is a well-loved name at sea. A Seabright cruise is all about creating a relaxed, memorable holiday, and every ship is designed to keep the good times going. On a Seabright ship there is always so much to do. On deck there are pools, waterslides, mini golf, a seaside theatre. Seabright Cruise Line has sailed for many years and is a well-loved name at sea. A Seabright cruise is all about creating a relaxed, memorable holiday, and every ship is designed to keep the good times going. On a Seabright ship there is always so much to do. On deck there are pools, waterslides, mini golf, a seaside theatre. Seabright Cruise Line has sailed for many years and is a well-loved name at sea. A Seabright cruise is all about creating a relaxed, memorable holiday, and every ship is designed to keep the good times going. On a Seabright ship there is always so much to do. On deck there are pools, waterslides, mini golf, a seaside theatre.</p>
    </div>

    <h2 class="abs partners-h">OUR RELIABLE PARTNERS</h2>
    <div class="abs arrows">
      <i><svg width="6" height="10" viewBox="0 0 6 10"><path d="M5 1L1 5l4 4" fill="none" stroke="#888" stroke-width="1.3"/></svg></i>
      <i><svg width="6" height="10" viewBox="0 0 6 10"><path d="M1 1l4 4-4 4" fill="none" stroke="#888" stroke-width="1.3"/></svg></i>
    </div>
    <div class="abs partners" aria-label="Partner badges">
      <span><i style="background:#c9353a"></i></span><span><i style="background:#1f55a8"></i></span><span><i style="background:#4a6a8a"></i></span><span><i style="background:#f39a2a"></i></span><span><i style="background:#3fa9e0"></i></span><span><i style="background:#2a78c8"></i></span>
    </div>
  </main>

  <footer class="abs footer">
    <div class="fcol" style="left:27px"><h4>Useful Pages</h4><ul><li>About Us</li><li>Contact us</li><li>Blog</li><li>FAQ</li><li>Terms of Service</li><li>Payment info</li><li>Reward Points</li></ul></div>
    <div class="fcol" style="left:188px"><h4>Cruise Infov</h4><ul><li>Cruise news</li><li>Visa</li><li>Honeymoon cruises</li><li>Firsttime on a Cruise</li></ul></div>
    <div class="fcol" style="left:344px;top:31px"><h4>About bluewake.example</h4>
      <div class="about-logo"><i></i><b>Bluewake</b></div>
      <p class="about-text">We're the most advanced cruise booking providr in china.</p>
    </div>
    <div class="fcol contact" style="left:599px;top:31px"><h4>Contact Us</h4>
      <p>Tidemark Studio Pte Ltd<br>Harbourline Centre 18, Quay Road 7<br>Portvale 20418 Coastland</p>
      <div class="line"><svg width="13" height="10" viewBox="0 0 13 10"><path d="M1 4c0-3 11-3 11 0l-2 1-1-2H4L3 5zM3 5h7l1 4H2z" fill="#fff"/></svg>(123) 555-0147 - (123) 555-0182</div>
      <div class="line"><svg width="13" height="10" viewBox="0 0 13 10"><rect x=".5" y=".5" width="12" height="9" fill="#fff"/><path d="M1 1l5.5 4.5L12 1" fill="none" stroke="#3f79ae"/></svg>mail@bluewake.example</div>
    </div>
  </footer>
  <div class="abs bottom">© 2013. Bluewake. All rights reserved.</div>
</div>
</body>
</html>
```